Torvane Email Signature Banners – Fabrication Capability Series

www.Torvane.com.au is an Australian engineering and fabrication company specialising in fabrication and welding of :
steel piping spools,
skids and frames,
small volume process steel tanks
and general steel fabrication
We require four distinct banner designs for use in Microsoft Lintaro email signatures. Each banner will highlight a specific capability while maintaining a consistent brand identity.
Deliverables
Four banners total:
Piping Spools Fabrication – focus on precision welding and stainless steel pipework
Skid & Frames Fabrication – highlight skid systems and structural frames
Small Steel Tanks Fabrication – show fabricated tanks and workshop craftsmanship
General Fabrication Solutions – broad steel fabrication theme for company-wide use
Dimensions: 600–700 px wide × 100 px high
Format: PNG (preferred), small file size prefered
Resolution: 72 dpi
Background: non-transparent, industrial or workshop setting
Text examples:
1. Piping Spools Fabrication
Option A: “Expert Fabrication Solutions for Process Piping”
Option B: “Precision Welding for Complex Systems”
Option C: “Delivering Quality in Every Spool”
Option D: “Engineered for Flow, Built for Strength”
2. Skid & Frames Fabrication
Option A: “Custom Engineered Modular Systems”
Option B: “Built Strong. Designed Smart.”
Option C: “Reliable Frames for Industrial Performance”
Option D: “Modular Fabrication for Seamless Integration”
3. Small Steel Tanks Fabrication
Option A: “Precision Built for Your Needs”
Option B: “Compact Strength. Proven Durability.”
Option C: “Fabricated for Performance and Longevity”
Option D: “Small Tanks. Big Reliability.”
4. General Fabrication Solutions
Option A: “Quality Craftsmanship, Proven Results”
Option B: “Your Partner in Precision Fabrication”
Option C: “Engineering Excellence in Every Weld”
Option D: “Australian Fabrication. Global Standards.”
Style Direction
Clean, professional, and engineering‑focused
Use Torvane brand colours
Blend photo realism with vector clarity (no heavy gradients)
Include subtle industrial textures or workshop imagery
Typography: bold sans‑serif, legible at small scale
Usage Context
These banners will appear at the bottom of staff email signatures via Lintaro Email Signature Tool for Microsoft 365, so clarity and fast loading are essential. No Logo is required in the banners.
Reference
Existing Torvane signature is attached. Colour palette to match the signature style and logo.
Target Market(s)
Engineering and construction companies,
Industry/Entity Type
Engineering fabrication design
Look and feel

```html
<!DOCTYPE html>
<html lang="en">
<head>
<meta charset="utf-8">
<title>Small Steel Tanks Fabrication – Email Signature Banner</title>
<link rel="stylesheet" href="https://fonts.googleapis.com/css2?family=Poppins:wght@400;700&display=swap">
<style>
  :root {
    --brand-blue: #0b51a3;
    --canvas-bg: #ffffff;
    --photo-dark: #2b2a2c;
    --photo-mid: #5a4a3c;
    --photo-warm: #b8733a;
    --photo-spark: #f3c27a;
  }
  html, body {
    margin: 0;
    padding: 0;
    width: 1200px;
    height: 200px;
    overflow: hidden;
    background: var(--canvas-bg);
  }
  .banner {
    position: relative;
    width: 1200px;
    height: 200px;
    background: var(--canvas-bg);
    overflow: hidden;
    font-family: "Poppins", sans-serif;
    color: var(--brand-blue);
  }
  .banner__copy {
    position: absolute;
    left: 41px;
    top: 46px;
    z-index: 2;
  }
  .banner__title {
    margin: 0;
    font-weight: 700;
    font-size: 51px;
    line-height: 1;
    letter-spacing: -0.2px;
    white-space: nowrap;
  }
  .banner__tagline {
    margin: 20px 0 0;
    font-weight: 400;
    font-size: 40px;
    line-height: 1;
    white-space: nowrap;
  }
  .banner__photo {
    position: absolute;
    right: 0;
    top: 0;
    width: 450px;
    height: 200px;
    background:
      radial-gradient(ellipse 90px 60px at 78% 88%, var(--photo-spark) 0%, rgba(243,194,122,0.4) 45%, transparent 100%),
      radial-gradient(ellipse 140px 120px at 95% 35%, rgba(184,115,58,0.85) 0%, transparent 100%),
      linear-gradient(100deg, var(--photo-dark) 20%, var(--photo-mid) 55%, var(--photo-warm) 100%);
  }
  .banner__photo-fade {
    position: absolute;
    left: 0;
    top: 0;
    width: 80px;
    height: 200px;
    background: linear-gradient(90deg, var(--canvas-bg) 0%, rgba(255,255,255,0) 100%);
  }
</style>
</head>
<body>
  <div class="banner">
    <div class="banner__copy">
      <h1 class="banner__title">Small Steel Tanks Fabrication</h1>
      <p class="banner__tagline">“Compact Strength. Proven Durability.”</p>
    </div>
    <div class="banner__photo" role="img" aria-label="Welder in protective helmet and gloves welding steel in a workshop, with sparks and smoke">
      <div class="banner__photo-fade"></div>
    </div>
  </div>
</body>
</html>
```